Criação de Cartao de Visita para Computador & Internet
A empresa queria:
" Nossos clientes fazem o outsorcing da TI para nós, assim cuidamos de todos os recursos se serviços de TI, também vendemos hardwares e softwares "

```html
<!DOCTYPE html>
<html lang="pt-BR">
<head>
<meta charset="UTF-8">
<title>NVR Corp — Cartão de Visita</title>
<link href="https://fonts.googleapis.com/css2?family=Open+Sans:wght@400;600;700;800&display=swap" rel="stylesheet">
<style>
  :root{
    --bg:#e4e6e8;
    --paper:#ffffff;
    --blue:#1a8fd1;
    --blue-dark:#0f6fae;
    --blue-light:#5cb8e8;
    --grey-band:#c9ced3;
    --green:#6aa842;
    --red:#d8262b;
    --ink:#3c4249;
    --muted:#7b838b;
  }
  *{box-sizing:border-box;margin:0;padding:0}
  html,body{width:1200px;height:1200px;overflow:hidden}
  body{background:var(--bg);font-family:"Open Sans",Arial,sans-serif;color:var(--ink);position:relative}
  .card{position:absolute;left:150px;width:900px;height:514px;background:var(--paper);
    box-shadow:0 6px 22px rgba(0,0,0,.14);overflow:hidden}
  .card--front{top:56px}
  .card--back{top:630px}
  .band{position:absolute;inset:0;width:100%;height:100%}

  /* front */
  .brand{position:absolute;left:90px;top:150px;display:flex;align-items:center;gap:22px}
  .brand__dot{width:150px;height:150px;border-radius:50%;background:var(--blue)}
  .brand__name{font-size:44px;font-weight:800;color:var(--blue)}
  .contact{position:absolute;left:500px;top:92px;width:360px}
  .person{display:flex;align-items:center;gap:12px}
  .person__icon{width:42px;height:42px;background:var(--blue-dark);display:flex;align-items:center;justify-content:center}
  .person__name{font-size:30px;font-weight:600;color:var(--ink);line-height:1}
  .person__role{font-size:13px;color:var(--muted);margin-top:4px}
  .division{margin-top:12px;font-size:21px;font-weight:800;color:var(--red);letter-spacing:.3px}
  .lines{list-style:none;margin-top:10px}
  .lines li{display:flex;align-items:center;gap:10px;font-size:15px;margin-bottom:7px}
  .ico{width:22px;height:22px;background:var(--blue);flex:none;display:flex;align-items:center;justify-content:center}

  /* back */
  .col{position:absolute;top:70px;width:360px}
  .col--it{left:70px}
  .col--events{left:480px}
  .divider{position:absolute;left:450px;top:70px;width:2px;height:300px;background:var(--grey-band)}
  .col__title{font-size:26px;font-weight:800}
  .col--it .col__title{color:var(--green)}
  .col--events .col__title{color:var(--red)}
  .col__sub{font-size:13px;color:var(--muted);margin-top:2px}
  .services{list-style:none;margin-top:18px}
  .services li{position:relative;padding-left:20px;font-size:15px;font-weight:600;margin-bottom:10px;line-height:1.3}
  .services li::before{content:"";position:absolute;left:0;top:6px;width:9px;height:9px;border-radius:50%}
  .col--it .services li::before{background:var(--green)}
  .col--events .services li::before{background:var(--red)}
  .col--events .services li{margin-bottom:8px}
</style>
</head>
<body>

<section class="card card--front">
  <svg class="band" viewBox="0 0 900 514" preserveAspectRatio="none" aria-hidden="true">
    <polygon points="0,470 900,380 900,420 0,514" fill="var(--grey-band)"/>
    <polygon points="300,514 900,420 900,514" fill="var(--blue)"/>
    <polygon points="620,514 900,470 900,514" fill="var(--blue-dark)"/>
  </svg>
  <div class="brand">
    <span class="brand__dot"></span>
    <span class="brand__name">NVR Corp</span>
  </div>
  <div class="contact">
    <div class="person">
      <span class="person__icon">
        <svg width="24" height="24" viewBox="0 0 24 24"><circle cx="12" cy="8" r="4.5" fill="#fff"/><path d="M3 22c0-5 4-8 9-8s9 3 9 8z" fill="#fff"/></svg>
      </span>
      <div>
        <div class="person__name">Marina Tavares</div>
        <div class="person__role">Coordenadora de Eventos</div>
      </div>
    </div>
    <div class="division">DIVISÃO DE EVENTOS</div>
    <ul class="lines">
      <li><span class="ico"><svg width="14" height="14" viewBox="0 0 24 24"><path d="M6 2l4 5-2 3c1.5 3 3 4.5 6 6l3-2 5 4-3 4C10 21 3 14 2 5z" fill="#fff"/></svg></span>11 3240-5178 (SP)</li>
      <li><span class="ico"><svg width="14" height="14" viewBox="0 0 24 24"><path d="M6 2l4 5-2 3c1.5 3 3 4.5 6 6l3-2 5 4-3 4C10 21 3 14 2 5z" fill="#fff"/></svg></span>0800 612 4390 (Demais Localidades)</li>
      <li><span class="ico"><svg width="14" height="14" viewBox="0 0 24 24"><rect x="6" y="2" width="12" height="20" rx="2" fill="#fff"/><rect x="8" y="5" width="8" height="12" fill="var(--blue)"/></svg></span>11 97462-3815</li>
      <li><span class="ico"><svg width="14" height="14" viewBox="0 0 24 24"><rect x="2" y="5" width="20" height="14" fill="#fff"/><path d="M2 5l10 8 10-8" stroke="var(--blue)" stroke-width="2" fill="none"/></svg></span>contato@nvrcorp.com.br</li>
    </ul>
  </div>
</section>

<section class="card card--back">
  <svg class="band" viewBox="0 0 900 514" preserveAspectRatio="none" aria-hidden="true">
    <polygon points="0,470 900,400 900,440 0,514" fill="var(--grey-band)"/>
    <polygon points="0,514 0,490 900,430 900,514" fill="var(--blue)"/>
    <polygon points="450,514 900,460 900,514" fill="var(--blue-dark)"/>
  </svg>
  <div class="col col--it">
    <h2 class="col__title">DIVISÃO DE TI</h2>
    <p class="col__sub">Soluções em Tecnologia da Informação</p>
    <ul class="services">
      <li>Administração e Suporte de TI (Outsourcing)</li>
      <li>Cloud Solutions</li>
      <li>Cotação e Venda de Hardware e Software</li>
      <li>Segurança e Proteção de Dados</li>
    </ul>
  </div>
  <span class="divider"></span>
  <div class="col col--events">
    <h2 class="col__title">DIVISÃO DE EVENTOS</h2>
    <p class="col__sub">Soluções em gestão de eventos</p>
    <ul class="services">
      <li>Workshops</li>
      <li>Congressos</li>
      <li>Palestras</li>
      <li>Cursos</li>
      <li>Networking</li>
      <li>Convenções Empresariais</li>
    </ul>
  </div>
</section>

</body>
</html>
```